Book cover design, title is "Leave the Cubicle: Building Your Own Paycheck in One Year"

Design a cover for a book about freelancing. Example of my previous book's cover attached. Book title is "Leave the Cubicle: Building Your Own Paycheck in One Year". Looking to target people who have a 9-5 job but are seeking to try out freelancing as a way to supplement income and eventually quit their day job.

Target Market(s)

Looking to target people who have a 9-5 job but are seeking to try out freelancing as a way to supplement income and eventually quit their day job.

Industry/Entity Type

Consulting

Font styles to use
Serif
Sans Serif

Colors

Designer to choose colors to be used in the design.

Requirements
Must have
• I love these books covers...
• https://www.pagebarn.example/Tame-Notepile-Handbook-Sorting-Planning-ebook/dp/Q00XZRTMPA/ref=kl_ab?ie=UTF8
• https://www.pagebarn.example/Quiet-Dawn-Authors-Drafting-Doubles/dp/5830174926/ref=kl_ab?ie=UTF8
• https://www.pagebarn.example/Draft-True-Stories-Guide-Weeks-ebook/dp/Q00PL44KD7/ref=kl_ab?ie=UTF8
• https://www.pagebarn.example/Routine-Weaving-Tiny-Shifts-Moments/dp/1627093358/ref=kl_ab?ie=UTF8
• https://www.pagebarn.example/Sharpen-Each-Hour-Practical-ebook/dp/Q00WTN6HJS/ref=kl_ab?ie=UTF8
• https://www.pagebarn.example/Maker-Co-Complete-Thriving-Independent-ebook/dp/Q00918KVZE/ref=sr_1_4?ie=UTF8&qid=1627582273&sr=8-4&keywords=freelancing
Should not have
• Don't submit 3D renderings, just the front cover image please.

```html
<!DOCTYPE html>
<html lang="en">
<head>
<meta charset="UTF-8">
<title>Leave the Cubicle – Book Cover</title>
<link href="https://fonts.googleapis.com/css2?family=Bebas+Neue&family=Open+Sans:wght@300;400;700&display=swap" rel="stylesheet">
<style>
  :root {
    --page-bg: #e4e4e2;
    --cover-bg: #f4f4f3;
    --gold: #e8b01a;
    --ink: #1e1e1e;
    --muted-gold: #f1c445;
  }
  * { margin: 0; padding: 0; box-sizing: border-box; }
  html, body {
    width: 1200px;
    height: 819px;
    overflow: hidden;
    background: var(--page-bg);
  }
  .canvas {
    position: relative;
    width: 1200px;
    height: 819px;
  }
  .cover {
    position: absolute;
    left: 347px;
    top: 30px;
    width: 507px;
    height: 760px;
    background: var(--cover-bg);
    text-align: center;
  }
  .title {
    position: absolute;
    left: 0;
    right: 0;
    top: 58px;
    font-family: "Bebas Neue", sans-serif;
    font-weight: 400;
    color: var(--gold);
    line-height: 0.92;
  }
  .title-main {
    display: block;
    font-size: 112px;
    letter-spacing: 1px;
  }
  .title-sub {
    display: block;
    font-size: 68px;
    letter-spacing: 1px;
  }
  .subtitle {
    position: absolute;
    left: 0;
    right: 0;
    top: 232px;
    font-family: "Open Sans", sans-serif;
    font-weight: 400;
    font-size: 17px;
    line-height: 1.2;
    color: var(--ink);
    text-transform: uppercase;
  }
  .subtitle strong { font-weight: 700; }
  .cover-illustration {
    position: absolute;
    left: 148px;
    top: 300px;
    width: 211px;
    height: 290px;
  }
  .author {
    position: absolute;
    left: 0;
    right: 0;
    top: 652px;
    font-family: "Open Sans", sans-serif;
    font-weight: 400;
    font-size: 23px;
    color: var(--ink);
  }
</style>
</head>
<body>
  <div class="canvas">
    <section class="cover">
      <h1 class="title">
        <span class="title-main">Leave</span>
        <span class="title-sub">The Cubicle</span>
      </h1>
      <p class="subtitle">Building your own <strong>paycheck</strong><br>in <strong>one year</strong></p>
      <svg class="cover-illustration" role="img" aria-label="Illustration of a yellow wallet with a dollar sign and coins dropping into it" viewBox="0 0 211 290">
        <defs>
          <linearGradient id="illustration-fill" x1="0" y1="0" x2="0" y2="1">
            <stop offset="0" stop-color="var(--muted-gold)" stop-opacity="0.35"/>
            <stop offset="1" stop-color="var(--gold)"/>
          </linearGradient>
        </defs>
        <rect width="211" height="290" rx="18" fill="url(#illustration-fill)"/>
      </svg>
      <p class="author">Author Name</p>
    </section>
  </div>
</body>
</html>
```